Brightmoor Senior Living Marketing Brochure, Covid-19 Brochure, Introduction to our manager

We are a Senior Living Community that services Assisted living and memory care. We have a lot of New programs for Activities, Food recipes, therapy, family and resident interaction , covid free, and want to introduce this to the community and existing family members.

Target Market(s)

La Jolla and San Diego for Brightmoor Senior Living and Memory Care of La Jolla and For Brightmoor Senior Living and Memory Care of Tarzana , San Fernando valley, tarzana, Encino , Woodland Hills Sherman oaks

Industry/Entity Type

Assisted Living

Other font styles liked:
• TBD

Colors
a54499
f7f3f9
ffffff
fece3e
ffc214

Requirements
Must have
• Product names for our marketing brochure , facility images per location

```html
<!DOCTYPE html>
<html lang="en">
<head>
<meta charset="utf-8">
<title>Brightmoor Senior Living – Brochure Set</title>
<link href="https://fonts.googleapis.com/css2?family=Montserrat:wght@400;500;600;700;800&family=Oswald:wght@300;400&family=Anton&display=swap" rel="stylesheet">
<style>
:root{
  --magenta:#a54499;
  --magenta-deep:#8e1f6e;
  --lilac:#f7f3f9;
  --white:#ffffff;
  --gold:#fece3e;
  --gold-deep:#d9b04a;
  --ink:#2b2b2b;
  --grey-panel:#ebebeb;
  --backdrop:#b4b4b4;
}
*{box-sizing:border-box;margin:0;padding:0}
html,body{width:1200px;height:2447px;overflow:hidden}
body{background:var(--backdrop);font-family:"Montserrat",sans-serif;color:var(--ink);position:relative}
.flyer{position:absolute;width:540px;overflow:hidden;background:var(--white);box-shadow:0 2px 8px rgba(0,0,0,.18)}
.flyer-intro{left:40px;top:428px;height:765px}
.flyer-assisted{left:620px;top:428px;height:765px}
.flyer-covid{left:330px;top:1253px;height:762px}
.sheet{position:absolute;left:0;top:0;width:482px;height:682px;transform-origin:0 0;transform:scale(1.1203)}
.flyer-covid .sheet{width:486px;height:686px;transform:scale(1.1111)}
.abs{position:absolute}
.shapes{position:absolute;left:0;top:0}
.photo{position:absolute}
.brand{position:absolute;font-weight:600;color:var(--gold-deep);letter-spacing:.3px;white-space:nowrap}
.brand-dot{display:inline-block;width:8px;height:8px;border-radius:50%;background:var(--magenta);margin-right:5px;vertical-align:middle}
.foot-contact{position:absolute;color:var(--white);font-size:10.5px;font-weight:600;line-height:15px}
.foot-contact small{display:block;font-size:8px;font-weight:600}
.follow{position:absolute;font-size:7.5px;color:var(--ink);white-space:nowrap}
.tick{display:inline-block;width:9px;height:9px;margin-right:6px;vertical-align:-1px;flex:none}

/* intro flyer */
.hero-copy{left:28px;top:118px;width:190px;color:var(--white)}
.hero-copy .pre{font-size:20px;font-weight:400;letter-spacing:.5px}
.hero-copy .big{font-size:35px;font-weight:800;color:var(--gold);line-height:36px}
.hero-copy .sub{font-size:13.5px;font-weight:700;letter-spacing:.4px}
.hero-copy .rule{width:34px;height:2px;background:var(--gold);margin:8px 0 10px}
.hero-copy p{font-size:6.4px;line-height:8.4px}
.sec-title{font-size:13.5px;font-weight:700;color:var(--magenta-deep);letter-spacing:.3px}
.sec-title b{display:block;color:var(--ink);font-weight:700}
.sec-rule{width:26px;height:2px;background:var(--gold-deep);margin-top:6px}
.body-copy{font-size:7.2px;line-height:9px}
.dining{left:28px;top:438px;width:196px;height:59px;background:var(--gold-deep);display:flex}
.dining span{flex:1;display:flex;align-items:center;justify-content:center;text-align:center;font-size:10px;font-weight:500;color:var(--ink)}
.dining span+span{border-left:1px solid rgba(0,0,0,.15)}
.amenities{left:257px;top:376px;width:203px;height:259px;background:var(--grey-panel);border-radius:6px;padding:18px 10px 0 14px}
.amenities li{list-style:none;display:flex;font-size:7.2px;line-height:9px;margin-bottom:8.5px}
.amenities li::before{content:"";flex:none;width:6px;height:6px;border-radius:50%;background:var(--magenta);margin:1px 9px 0 0}

/* assisted flyer */
.assisted-title{left:0;top:40px;width:482px;text-align:center;font-size:21px;font-weight:700;letter-spacing:.5px}
.assisted-title em{font-style:normal;color:var(--magenta-deep)}
.assess-head{left:0;top:226px;width:482px;text-align:center;font-size:13.5px;font-weight:700;color:var(--magenta-deep);letter-spacing:.3px}
.assess-head b{display:block;color:var(--ink)}
.assess-head .sec-rule{margin:6px auto 0}
.assess-list{font-size:6.6px;line-height:8px}
.assess-list li{list-style:none;display:flex;margin-bottom:8px}
.assess-list li::before{content:"";flex:none;width:6px;height:6px;border-radius:50%;background:var(--magenta);margin:1px 12px 0 0}
.values{left:0;top:495px;width:482px;height:126px;background:var(--grey-panel);display:flex;padding:12px 14px 0 30px;gap:20px}
.values div{flex:1;font-size:6.6px;line-height:8px}
.values p{display:flex;margin-bottom:9px}

/* covid flyer */
.covid-copy{left:256px;top:58px;width:220px;color:var(--white)}
.covid-copy .pre{font-size:16px;font-weight:300;font-family:"Oswald",sans-serif;letter-spacing:.4px}
.covid-copy .corona{font-family:"Oswald",sans-serif;font-weight:300;font-size:46px;line-height:50px;color:var(--gold);letter-spacing:1px}
.covid-copy .virus{font-family:"Anton",sans-serif;font-size:80px;line-height:82px;letter-spacing:1px}
.covid-copy .rule{width:24px;height:2px;background:var(--gold);margin:10px 0 14px}
.covid-copy .note{font-size:10.5px;font-weight:400}
.gold-title{font-size:13.5px;font-weight:700;color:var(--gold-deep);letter-spacing:.4px}
.mag-rule{width:26px;height:2px;background:var(--magenta-deep);margin-top:6px}
.prevent{left:272px;top:360px;width:200px}
.prevent .item{display:flex;margin-bottom:17px}
.prevent .ico{flex:none;width:20px;height:20px;border:1.5px solid var(--gold-deep);border-radius:50%;margin:0 10px 0 0}
.prevent h4{font-size:11px;font-weight:700;letter-spacing:.3px;margin-bottom:4px}
.prevent p{font-size:7.2px;line-height:9px}
.covid-ticks p{display:flex;font-size:7.2px;line-height:9px;margin-bottom:12px}
</style>
</head>
<body>

<!-- ============ Flyer 1 : community introduction ============ -->
<section class="flyer flyer-intro">
  <div class="sheet">
    <div class="photo" style="left:0;top:0;width:482px;height:300px;background:linear-gradient(120deg,#1d2243 0%,#5a4a3a 40%,#c9a45e 70%,#e9cf8d 100%)" role="img" aria-label="Photo of a grandfather and young grandson sharing a moment in warm golden light"></div>
    <svg class="shapes" width="482" height="682" viewBox="0 0 482 682" aria-hidden="true">
      <path d="M222 0H482V78H278Q238 78 222 0Z" fill="#fff"/>
      <rect x="0" y="220" width="120" height="82" fill="#d9b04a"/>
      <path d="M0 75H160Q230 75 230 145V300H62Q0 300 0 240Z" fill="#a54499"/>
      <path d="M0 75H160Q230 75 230 145V300H62Q0 300 0 240Z" fill="#8e1f6e" opacity=".35"/>
      <rect x="0" y="299" width="482" height="3" fill="#d9b04a"/>
      <rect x="0" y="302" width="482" height="8" fill="#f7f3f9"/>
      <rect x="28" y="510" width="94" height="102" fill="#d9b04a"/>
      <rect x="130" y="510" width="94" height="102" fill="#d9b04a"/>
      <path d="M0 628H238Q266 628 282 650Q298 672 330 672H482V682H0Z" fill="#a54499"/>
      <path d="M238 628Q266 628 282 650Q298 672 330 672H482" fill="none" stroke="#d9b04a" stroke-width="3"/>
    </svg>
    <div class="brand" style="left:266px;top:32px;font-size:12.5px"><span class="brand-dot"></span>Brightmoor Senior Living</div>

    <div class="abs hero-copy">
      <div class="pre">A LUXURIOUS</div>
      <div class="big">SENIOR</div>
      <div class="sub">LIVING COMMUNITY</div>
      <div class="rule"></div>
      <p>At Brightmoor, we know that each senior who comes through our doors has a unique set of interests and needs. We provide living arrangements that suit your lifestyle with various levels of care and personal assistance.</p>
    </div>

    <div class="abs" style="left:28px;top:326px;width:200px">
      <h2 class="sec-title">MARKETING</h2>
      <div class="sec-rule"></div>
      <p class="body-copy" style="margin-top:10px">over 125 channels included premium cable and sports.</p>
      <p class="body-copy" style="margin-top:8px">Outdoor activities including an 8 hole putting green and BBQ COURTYARD.</p>
      <p style="font-size:9px;font-weight:600;margin-top:9px">Logo Here</p>
    </div>
    <div class="abs dining"><span>Hawthorne<br>Restaurant</span><span>The Garden Café</span></div>
    <div class="photo" style="left:30px;top:512px;width:90px;height:98px;background:linear-gradient(#3a64b8,#c9b79a 55%,#7d6a55)" role="img" aria-label="Photo of the community entrance with a lit canopy"></div>
    <div class="photo" style="left:132px;top:512px;width:90px;height:98px;background:linear-gradient(#2f5fbf,#e8d6b4 55%,#7c8a5a)" role="img" aria-label="Photo of the community building exterior with landscaped sign"></div>

    <div class="abs" style="left:257px;top:320px;width:210px">
      <h2 class="sec-title">SALON FOR NAILS<b>HAIR AND MASSAGES</b></h2>
      <div class="sec-rule"></div>
    </div>
    <ul class="abs amenities">
      <li>Housekeeping And Laundry Services</li>
      <li>Emergency Alert System</li>
      <li>Daily Activity Schedule</li>
      <li>Beauty Salon And Barber Shop</li>
      <li>Luxury Transportation: Executive Shuttle Vans and Touring Minivans And Valet Services</li>
      <li>General Store</li>
      <li>Skyline TV Premium Package – Premium Sports Package, CinePrime, StarScreen And More!</li>
      <li>Movie Theatre, Shuffle Board, Pool Table And Outdoor BBQ</li>
      <li>Virtual Reality Station</li>
    </ul>

    <div class="foot-contact" style="left:28px;top:641px">☏ (555) 201-4400 / (555) 307-8812<small>◉ www.brightmoorseniorliving.com</small></div>
    <div class="follow" style="left:405px;top:646px">follow us</div>
  </div>
</section>

<!-- ============ Flyer 2 : assisted living ============ -->
<section class="flyer flyer-assisted">
  <div class="sheet">
    <div class="photo" style="left:0;top:22px;width:482px;height:188px;background:linear-gradient(90deg,#d9cbb6,#f1ebe2 30%,#e6dccd 60%,#cfc3b0)" role="img" aria-label="Photo of smiling seniors doing seated stretching exercises with raised arms"></div>
    <svg class="shapes" width="482" height="682" viewBox="0 0 482 682" aria-hidden="true">
      <rect x="0" y="0" width="482" height="22" fill="#fff"/>
      <path d="M0 22H60Q14 40 0 110Z" fill="#d9b04a"/>
      <path d="M95 22H420Q408 70 360 74H150Q104 70 95 22Z" fill="#fff"/>
      <path d="M482 110V212H395Q470 200 482 110Z" fill="#a54499"/>
      <rect x="0" y="210" width="482" height="3" fill="#d9b04a"/>
      <path d="M0 628H238Q266 628 282 650Q298 672 330 672H482V682H0Z" fill="#a54499"/>
      <path d="M238 628Q266 628 282 650Q298 672 330 672H482" fill="none" stroke="#d9b04a" stroke-width="3"/>
    </svg>
    <h1 class="abs assisted-title"><em>ASSISTED</em> LIVING</h1>
    <div class="abs assess-head">MULTIPLE RESIDENT ASSESSMENTS BASED<b>ON SERVICE TYPES</b><div class="sec-rule"></div></div>

    <ul class="abs assess-list" style="left:30px;top:280px;width:190px">
      <li>Multiple Resident Assessments based on Service Types</li>
      <li>Resident Task Scheduling and Service Plans</li>
      <li>End of Shift Reporting</li>
      <li>Resident Care Threads</li>
      <li>Resident Focus Areas and Incident Tracking and Reporting</li>
      <li>Meaningful and Customizable Dashboards</li>
      <li>Availability of standardized Focus Areas and Follow up Protocols</li>
      <li>Cost of Care Variance Reporting</li>
      <li>customized Assessments (based on flexible points, time, or flat rate)</li>
      <li>eMAR</li>
    </ul>
    <ul class="abs assess-list" style="left:262px;top:280px;width:195px">
      <li>Acuity Analysis</li>
      <li>State Forms and Reporting</li>
      <li>Scheduled care (includes non-assessment related tasks such as physician visits, TB testing, etc.)</li>
      <li>Acuity levels</li>
      <li>Staffing needs analysis for your Assisted Living, Memory Care or CCRC community is based on up-to-date resident assessments.</li>
      <li>Document resident risks, past incidents, individual behaviors, preferences, and additional family and caregiver input.</li>
      <li>Family and Resident Portal</li>
      <li>Brightmoor Senior Living is overcoming social isolation through the power of virtual reality and shared experiences.</li>
    </ul>

    <div class="abs values">
      <div>
        <p><svg class="tick" viewBox="0 0 10 10"><circle cx="5" cy="5" r="4.3" fill="none" stroke="#d9b04a"/><path d="M3 5.2l1.4 1.4L7.2 3.8" fill="none" stroke="#d9b04a"/></svg>Living</p>
        <p><svg class="tick" viewBox="0 0 10 10"><circle cx="5" cy="5" r="4.3" fill="none" stroke="#d9b04a"/><path d="M3 5.2l1.4 1.4L7.2 3.8" fill="none" stroke="#d9b04a"/></svg>Relive</p>
        <p><svg class="tick" viewBox="0 0 10 10"><circle cx="5" cy="5" r="4.3" fill="none" stroke="#d9b04a"/><path d="M3 5.2l1.4 1.4L7.2 3.8" fill="none" stroke="#d9b04a"/></svg><span>Customized reminiscence therapy tools allow your residents to take a stroll down memory lane by revisiting their childhood home, wedding location or anywhere else from their past.</span></p>
      </div>
      <div>
        <p><svg class="tick" viewBox="0 0 10 10"><circle cx="5" cy="5" r="4.3" fill="none" stroke="#d9b04a"/><path d="M3 5.2l1.4 1.4L7.2 3.8" fill="none" stroke="#d9b04a"/></svg>Connect</p>
        <p><svg class="tick" viewBox="0 0 10 10"><circle cx="5" cy="5" r="4.3" fill="none" stroke="#d9b04a"/><path d="M3 5.2l1.4 1.4L7.2 3.8" fill="none" stroke="#d9b04a"/></svg>Reconnect</p>
        <p><svg class="tick" viewBox="0 0 10 10"><circle cx="5" cy="5" r="4.3" fill="none" stroke="#d9b04a"/><path d="M3 5.2l1.4 1.4L7.2 3.8" fill="none" stroke="#d9b04a"/></svg><span>Provide opportunities for your loved ones to virtually leave the four walls of our community to check off bucket list items and engage with the world in ways they never thought possible.</span></p>
      </div>
      <div>
        <p><svg class="tick" viewBox="0 0 10 10"><circle cx="5" cy="5" r="4.3" fill="none" stroke="#d9b04a"/><path d="M3 5.2l1.4 1.4L7.2 3.8" fill="none" stroke="#d9b04a"/></svg>Lightbulb</p>
        <p><svg class="tick" viewBox="0 0 10 10"><circle cx="5" cy="5" r="4.3" fill="none" stroke="#d9b04a"/><path d="M3 5.2l1.4 1.4L7.2 3.8" fill="none" stroke="#d9b04a"/></svg>Reinspire</p>
        <p><svg class="tick" viewBox="0 0 10 10"><circle cx="5" cy="5" r="4.3" fill="none" stroke="#d9b04a"/><path d="M3 5.2l1.4 1.4L7.2 3.8" fill="none" stroke="#d9b04a"/></svg><span>Create new friendships through the power of shared experience, all while providing unforgettable moments and stories that residents and their families will remember forever.</span></p>
      </div>
    </div>

    <div class="foot-contact" style="left:28px;top:641px">☏ (555) 201-4400 / (555) 307-8812<small>◉ www.brightmoorseniorliving.com</small></div>
    <div class="brand" style="left:290px;top:646px;font-size:7.5px">Brightmoor Senior Living</div>
    <div class="follow" style="left:405px;top:646px">follow us</div>
  </div>
</section>

<!-- ============ Flyer 3 : covid-19 ============ -->
<section class="flyer flyer-covid">
  <div class="sheet">
    <svg class="shapes" width="486" height="686" viewBox="0 0 486 686" aria-hidden="true">
      <rect x="0" y="0" width="486" height="318" fill="#a54499"/>
      <path d="M250 0H486V26H290Q262 26 250 0Z" fill="#fff"/>
      <path d="M250 0Q262 26 290 26H486" fill="none" stroke="#d9b04a" stroke-width="3"/>
      <path d="M0 628H246Q272 628 288 655Q302 678 330 678H486V686H0Z" fill="#a54499"/>
      <path d="M246 628Q272 628 288 655Q302 678 330 678H486" fill="none" stroke="#d9b04a" stroke-width="3"/>
    </svg>
    <div class="photo" style="left:0;top:20px;width:250px;height:298px;background:linear-gradient(160deg,#c98fb8,#e7cdbf 45%,#b98e84 80%,#8e6f6b)" role="img" aria-label="Photo of an elderly couple wearing face masks"></div>
    <div class="abs covid-copy">
      <div class="pre">Make Social Distance For</div>
      <div class="corona">CORONA</div>
      <div class="virus">VIRUS</div>
      <div class="rule"></div>
      <div class="note">If you have symptoms wear a Mask</div>
    </div>

    <div class="abs" style="left:28px;top:336px;width:200px">
      <h2 class="gold-title">WHAT IS COVID-19?</h2>
      <div class="mag-rule"></div>
      <p class="body-copy" style="margin-top:18px">Lorem Ipsum is simply dummy text of the printing and typesetting industry. Lorem Ipsum has been the industry's standard dummy text ever since the 1500s, when an unknown printer took a galley of type and scrambled it to make a type specimen book.</p>
      <div class="covid-ticks" style="margin-top:18px">
        <p><svg class="tick" viewBox="0 0 10 10"><circle cx="5" cy="5" r="4.3" fill="none" stroke="#a54499"/><path d="M3 5.2l1.4 1.4L7.2 3.8" fill="none" stroke="#a54499"/></svg><span>Lorem Ipsum is simply dummy text of the printing and typesetting industry.</span></p>
        <p><svg class="tick" viewBox="0 0 10 10"><circle cx="5" cy="5" r="4.3" fill="none" stroke="#a54499"/><path d="M3 5.2l1.4 1.4L7.2 3.8" fill="none" stroke="#a54499"/></svg><span>Lorem Ipsum is simply dummy text of the printing and typesetting industry.</span></p>
      </div>
    </div>
    <div class="photo" style="left:28px;top:510px;width:94px;height:102px;background:linear-gradient(135deg,#7fb6d8,#e8eef2 60%,#b7c7d3)" role="img" aria-label="Photo of a nurse in protective gear caring for a senior patient"></div>
    <div class="photo" style="left:132px;top:510px;width:94px;height:102px;background:linear-gradient(135deg,#e3e5e8,#f5f5f5 55%,#d8c27a)" role="img" aria-label="Photo of a worker in a protective suit disinfecting a room"></div>

    <div class="abs" style="left:272px;top:326px">
      <h2 class="gold-title">PREVENTATION</h2>
      <div class="mag-rule"></div>
    </div>
    <div class="abs prevent">
      <div class="item"><span class="ico"></span><div><h4>USING MASK</h4><p>Lorem Ipsum is simply dummy text of the printing and typesetting industry.</p></div></div>
      <div class="item"><span class="ico"></span><div><h4>WASH HAND</h4><p>Lorem Ipsum is simply dummy text of the printing and typesetting industry.</p></div></div>
      <div class="item"><span class="ico"></span><div><h4>COOK MEAT</h4><p>Lorem Ipsum is simply dummy text of the printing and typesetting industry.</p></div></div>
      <div class="item"><span class="ico"></span><div><h4>GO TO DOCTOR</h4><p>Lorem Ipsum is simply dummy text of the printing and typesetting industry.</p></div></div>
    </div>
    <div class="brand" style="left:272px;top:616px;font-size:12px"><span class="brand-dot"></span>Brightmoor Senior Living</div>

    <div class="foot-contact" style="left:28px;top:644px">☏ (555) 201-4400 / (555) 307-8812<small>◉ www.brightmoorseniorliving.com</small></div>
    <div class="follow" style="left:316px;top:656px">follow us</div>
  </div>
</section>

</body>
</html>
```